Brookvane Consulting Business Card Design

Business Card Design for Brookvane Consulting. Brookvane Consulting is a boutique consultancy based in Atlanta, GA., that specializes in marketing strategy, organization planning, and leadership development. We provide solutions for small businesses and startups as well as Vantage 300 companies.

http://brookvaneconsulting.com/

Target Market(s)

We provide solutions for small businesses and startups as well as Vantage 300 companies.

Industry/Entity Type

Consulting

Contact Information for Business Card

Two sided business card with priority on contact information, logo, tag line (Room to Think Bigger, Act Sooner, Grow Further)

Colors

Designer to choose colors to be used in the design.

Requirements
Must have
• contact information, logo, tag line (Room to Think Bigger, Act Sooner, Grow Further)
• Simple no over communication.
Nice to have
• I would like to see different placements of logo and creative use of both sides of the card
Should not have
• Do not put too much information on the card.

```html
<!DOCTYPE html>
<html lang="en">
<head>
<meta charset="utf-8">
<title>Brookvane Consulting Business Card</title>
<link rel="stylesheet" href="https://fonts.googleapis.com/css2?family=Open+Sans:wght@400;600;700&display=swap">
<style>
  :root {
    --backdrop: #2a2a2a;
    --card: #363636;
    --card-front: #3a3a3a;
    --band: #0d0d0d;
    --stripe: #9a9a9a;
    --stripe-soft: #5a5a5a;
    --ink: #ffffff;
    --front-name: #cfcfcf;
  }
  * { box-sizing: border-box; margin: 0; padding: 0; }
  html, body { width: 799px; height: 1200px; overflow: hidden; }
  body {
    background: var(--backdrop);
    font-family: "Open Sans", Arial, sans-serif;
    position: relative;
  }
  .card {
    position: absolute;
    left: 80px;
    width: 640px;
    height: 366px;
    border-radius: 24px;
    overflow: hidden;
    box-shadow: 0 18px 40px rgba(0,0,0,0.45);
  }
  .card-front { top: 110px; background: var(--card-front); }
  .card-back { top: 700px; background: var(--card); }

  .front-brand {
    position: absolute;
    inset: 0;
    display: flex;
    align-items: center;
    justify-content: center;
    gap: 14px;
  }
  .brand-mark { width: 22px; height: 22px; background: var(--front-name); }
  .front-brand .brand-name {
    font-size: 40px;
    font-weight: 600;
    color: var(--front-name);
    letter-spacing: 0.5px;
  }

  .back-waves { position: absolute; inset: 0; }
  .back-brand {
    position: absolute;
    left: 40px;
    top: 110px;
    display: flex;
    align-items: center;
    gap: 12px;
  }
  .back-brand .brand-mark { width: 18px; height: 18px; background: var(--ink); }
  .back-brand .brand-name {
    font-size: 30px;
    font-weight: 600;
    color: var(--ink);
  }
  .tagline {
    position: absolute;
    right: 34px;
    top: 72px;
    text-align: right;
    font-size: 14px;
    font-weight: 600;
    line-height: 1.35;
    color: var(--ink);
  }
  .contact {
    position: absolute;
    left: 40px;
    top: 200px;
    list-style: none;
    font-size: 14px;
    line-height: 1.45;
    color: var(--ink);
  }
  .signature {
    position: absolute;
    right: 40px;
    bottom: 30px;
    font-size: 20px;
    font-weight: 700;
    color: var(--ink);
  }
</style>
</head>
<body>
  <section class="card card-front" aria-label="Card front">
    <div class="front-brand">
      <span class="brand-mark"></span>
      <span class="brand-name">Brookvane Consulting</span>
    </div>
  </section>

  <section class="card card-back" aria-label="Card back">
    <svg class="back-waves" viewBox="0 0 640 366" preserveAspectRatio="none" aria-hidden="true">
      <path d="M0 0 H640 V270 C560 250 500 200 440 130 C380 60 250 20 0 25 Z" fill="var(--band)"/>
      <path d="M20 30 C250 28 380 70 440 140 C500 210 560 255 640 272" fill="none" stroke="var(--stripe)" stroke-width="9"/>
      <path d="M160 40 C300 40 390 80 450 150" fill="none" stroke="var(--stripe-soft)" stroke-width="3"/>
    </svg>
    <div class="back-brand">
      <span class="brand-mark"></span>
      <span class="brand-name">Brookvane Consulting</span>
    </div>
    <p class="tagline">Room to Think Bigger,<br>Act Sooner, Grow Further</p>
    <ul class="contact">
      <li>404-555-0173</li>
      <li>dara@brookvaneconsulting.com</li>
      <li>www.brookvaneconsulting.com</li>
    </ul>
    <p class="signature">Dara</p>
  </section>
</body>
</html>
```